Design a compelling Tarnwove Business Card that will drive people to my site

I want a business card that I can give to people—less to tell them who I am and more to direct them to my website. My website is a portal for Pelmor Aquatics Officials and a place for people who want to become Pelmor Aquatics Officials.
I am uploading my official company logo as well as a business card mockup that I did on my own. Please feel free to completely stray from this design.
I've included a screen recording of the homepage of my website as well.
Target Market(s)
Pelmor Aquatics Officials and people who desire to become one
Contact Information for Business Card
website url
Look and feel
Each slider illustrates characteristics of the customer's brand and the style your logo design should communicate.

```html
<!DOCTYPE html>
<html lang="en">
<head>
<meta charset="utf-8">
<title>Tarnwove Business Card</title>
<link href="https://fonts.googleapis.com/css2?family=Montserrat:wght@400;500;700&display=swap" rel="stylesheet">
<style>
  :root {
    --stage: #d3d3d3;
    --brand-blue: #3a55a5;
    --brand-light: #8fa3d8;
    --paper: #ffffff;
    --ink: #2b2b2b;
  }
  html, body {
    margin: 0;
    padding: 0;
    width: 1200px;
    height: 802px;
    overflow: hidden;
    background: var(--stage);
    font-family: "Montserrat", sans-serif;
  }
  .sheet {
    position: relative;
    width: 1200px;
    height: 802px;
  }
  .card {
    position: absolute;
    top: 250px;
    width: 530px;
    height: 303px;
    border-radius: 18px;
    overflow: hidden;
    box-shadow: 0 10px 24px rgba(0,0,0,0.18);
  }
  .card--front { left: 50px; background: var(--paper); }
  .card--back  { left: 620px; background: var(--brand-blue); }

  .card__wave {
    position: absolute;
    inset: 0;
    width: 100%;
    height: 100%;
  }
  .card__tab {
    position: absolute;
    top: 0;
    right: 28px;
    width: 22px;
    height: 30px;
    background: var(--brand-light);
  }
  .holder {
    position: absolute;
    top: 44px;
    right: 40px;
    text-align: right;
  }
  .holder__name {
    margin: 0;
    font-size: 21px;
    font-weight: 700;
    color: var(--brand-blue);
    letter-spacing: 0.2px;
  }
  .holder__name span { color: var(--brand-light); }
  .holder__role {
    margin: 2px 0 0;
    font-size: 12px;
    font-weight: 400;
    color: var(--ink);
  }
  .wordmark {
    position: absolute;
    display: flex;
    align-items: center;
    gap: 10px;
    font-weight: 700;
    color: var(--brand-blue);
    letter-spacing: -0.5px;
  }
  .wordmark__dot {
    border-radius: 50%;
    background: currentColor;
  }
  .card--front .wordmark { left: 34px; top: 104px; font-size: 46px; }
  .card--front .wordmark__dot { width: 14px; height: 14px; }
  .card--back .wordmark {
    left: 50%;
    top: 50%;
    transform: translate(-50%, -50%);
    font-size: 70px;
    color: var(--paper);
  }
  .card--back .wordmark__dot { width: 20px; height: 20px; }
  .contact {
    position: absolute;
    left: 38px;
    top: 196px;
    margin: 0;
    padding: 0;
    list-style: none;
    font-size: 13px;
    color: var(--ink);
  }
  .contact__item {
    display: flex;
    align-items: center;
    gap: 8px;
    margin-bottom: 7px;
  }
  .contact__icon { width: 13px; height: 13px; fill: var(--brand-blue); }
</style>
</head>
<body>
<main class="sheet">
  <section class="card card--front" aria-label="Business card front">
    <svg class="card__wave" viewBox="0 0 530 303" preserveAspectRatio="none" aria-hidden="true">
      <path d="M0,303 L0,292 C150,302 270,262 370,170 C435,110 480,90 530,84 L530,303 Z" fill="#3a55a5"/>
      <path d="M0,284 C150,294 262,252 362,160 C428,100 476,80 530,74" fill="none" stroke="#8fa3d8" stroke-width="4"/>
    </svg>
    <div class="card__tab"></div>
    <div class="holder">
      <h1 class="holder__name">Dorian <span>Malvesti</span></h1>
      <p class="holder__role">CEO &amp; Founder</p>
    </div>
    <div class="wordmark"><span class="wordmark__dot"></span>tarnwove</div>
    <ul class="contact">
      <li class="contact__item">
        <svg class="contact__icon" viewBox="0 0 16 16"><path d="M3.5 1h3l1.2 3.6-2 1.4a9 9 0 0 0 4.3 4.3l1.4-2L15 9.5v3A2.5 2.5 0 0 1 12.5 15 11.5 11.5 0 0 1 1 3.5 2.5 2.5 0 0 1 3.5 1z"/></svg>
        (555) 210-4473
      </li>
      <li class="contact__item">
        <svg class="contact__icon" viewBox="0 0 16 16"><path d="M1 3h14v10H1z M1 3l7 6 7-6" stroke="#fff" stroke-width="1"/></svg>
        dorian@tarnwove.com
      </li>
      <li class="contact__item">
        <svg class="contact__icon" viewBox="0 0 16 16"><circle cx="8" cy="8" r="7"/><path d="M1 8h14M8 1c-3 3-3 11 0 14M8 1c3 3 3 11 0 14" stroke="#fff" stroke-width="1" fill="none"/></svg>
        www.tarnwove.com
      </li>
    </ul>
  </section>

  <section class="card card--back" aria-label="Business card back">
    <div class="wordmark"><span class="wordmark__dot"></span>tarnwove</div>
  </section>
</main>
</body>
</html>
```